Creation of a Valterna Flyer design

As part of the cr% 26 # 233; ation of our soci% 26 # 233; t% 26 # 233 ;, we wish to cr% 26 # 233; er a flyer pr% 26 # 233; feeling our diff% 26 # 233; annuities% 26 # 233; s business advisory services% 26 # 233; foreign% 26 # 232; res who wish to develop their activities% 26 # 233; s in Switzerland. We want a double-sided flyer that presents% 26 # 233; society% 26 # 233; t% 26 # 233; d% 26 # 39; a c% 26 # 244; t% 26 # 233; and who presents% 26 # 233; benefits of the other. We have d% 26 # 233; j% 26 # 224; made a very basic provisional flyer to be able to present our activities. We put it to you as an example.

Target Market(s)

European companies% 26 # 233; internal% 26 # 233; res% 26 # 233; es by the market% 26 # 233; Swiss

Industry/Entity Type

Business Consultant

Colors

Designer to choose colors to be used in the design.

Requirements
Must have
• Company name and contact details
A field to detail the services
Nice to have
• Some% 26 # 233; l% 26 # 233; elements that recall Switzerland and some% 26 # 233; l% 26 # 233; elements that recall c% 26 # 244; t% 26 # 233; % 26quot; business% 26quot;

```html
<!DOCTYPE html>
<html lang="en">
<head>
<meta charset="UTF-8">
<title>Valterna – Business advisory for the Swiss market</title>
<link href="https://fonts.googleapis.com/css2?family=Arimo:ital,wght@0,400;0,700;1,700&display=swap" rel="stylesheet">
<style>
  :root {
    --navy: #233f57;
    --sky-top: #f5f9fd;
    --sky-mid: #dbe9f8;
    --sky-blue: #6ea7e8;
    --town: #c9b9a3;
    --river: #3fa7a6;
    --white: #ffffff;
    --accent: #6fb2f0;
  }
  * { margin: 0; padding: 0; box-sizing: border-box; }
  html, body { width: 927px; height: 1200px; overflow: hidden; background: var(--white); }
  body { font-family: "Arimo", Arial, sans-serif; color: var(--navy); }
  .flyer { position: relative; width: 927px; height: 1200px; overflow: hidden; }

  .backdrop {
    position: absolute; inset: 0;
    background:
      linear-gradient(180deg, rgba(255,255,255,0) 0%, rgba(255,255,255,0) 64%, rgba(201,185,163,.55) 74%, rgba(63,167,166,.85) 88%, rgba(63,167,166,.9) 100%),
      linear-gradient(100deg, var(--sky-top) 0%, var(--sky-top) 42%, var(--sky-mid) 64%, var(--sky-blue) 100%);
  }

  .headline {
    position: absolute; left: 40px; top: 59px; width: 847px;
    text-align: center; font-weight: 700; font-style: italic;
    font-size: 28px; line-height: 35px; color: var(--navy); white-space: nowrap;
  }
  .intro {
    position: absolute; left: 105px; top: 187px; width: 770px;
    font-weight: 700; font-size: 16.3px; line-height: 21.7px; color: var(--navy); white-space: nowrap;
  }
  .service {
    position: absolute; left: 105px; width: 765px;
    font-size: 16.8px; line-height: 22px; font-weight: 400; color: var(--navy);
  }
  .tick { position: absolute; left: -27px; top: 3px; }

  .hex { position: absolute; }

  .footer-band { position: absolute; left: 0; top: 0; }
  .brand { position: absolute; left: 305px; top: 1019px; display: flex; align-items: center; gap: 22px; }
  .brand-square { width: 40px; height: 40px; background: var(--white); border-radius: 7px; }
  .brand-name { font-weight: 400; font-size: 31px; letter-spacing: 2px; color: var(--white); }
  .office {
    position: absolute; left: -18px; width: 927px; top: 1070px; text-align: center;
    font-weight: 700; font-size: 15.5px; line-height: 20px; color: var(--white);
  }
  .contacts {
    position: absolute; left: -10px; width: 927px; top: 1131px; text-align: center;
    font-weight: 700; font-size: 17.5px; letter-spacing: 3.2px; color: var(--white); white-space: nowrap;
  }
  .contacts .sep { color: var(--accent); margin: 0 10px; font-weight: 400; }
</style>
</head>
<body>
<div class="flyer">
  <div class="backdrop" role="img" aria-label="Photograph of a Swiss old town along a river under a bright blue summer sky"></div>

  <h1 class="headline">You are convinced of the potential of your product or<br>service and you wish to focus on the Swiss market,<br>or you want to expand your market share!</h1>

  <p class="intro">Thanks to its personalized approach and tailor-made assistance, Valterna offers you the<br>right support to develop your business activities and answers to all your questions about<br>the swiss market. As a partner we assist you in finding market opportunities:</p>

  <p class="service" style="top:267px"><svg class="tick" width="21" height="17" viewBox="0 0 21 17"><path d="M0 9 L3 6 L7 10 L18 0 L21 2 L7 16 Z" fill="var(--navy)"/></svg>By providing commercial contacts that match your target profiles</p>
  <p class="service" style="top:304px"><svg class="tick" width="21" height="17" viewBox="0 0 21 17"><path d="M0 9 L3 6 L7 10 L18 0 L21 2 L7 16 Z" fill="var(--navy)"/></svg>By listing the legal and regulatory requirements specific to the Swiss market (Switzerland is not<br>an EU member State);</p>
  <p class="service" style="top:362px"><svg class="tick" width="21" height="17" viewBox="0 0 21 17"><path d="M0 9 L3 6 L7 10 L18 0 L21 2 L7 16 Z" fill="var(--navy)"/></svg>By putting you in contact with private or public interlocutors in the context of an individual<br>contact programme;</p>
  <p class="service" style="top:414px"><svg class="tick" width="21" height="17" viewBox="0 0 21 17"><path d="M0 9 L3 6 L7 10 L18 0 L21 2 L7 16 Z" fill="var(--navy)"/></svg>By preparing a market study that measures the potential of your product or service;</p>
  <p class="service" style="top:451px"><svg class="tick" width="21" height="17" viewBox="0 0 21 17"><path d="M0 9 L3 6 L7 10 L18 0 L21 2 L7 16 Z" fill="var(--navy)"/></svg>By adapting your marketing material (website, brochures, flyers, etc.) to the specific needs of<br>the Swiss market and by translating it into German and/or French;</p>
  <p class="service" style="top:503px"><svg class="tick" width="21" height="17" viewBox="0 0 21 17"><path d="M0 9 L3 6 L7 10 L18 0 L21 2 L7 16 Z" fill="var(--navy)"/></svg>By organizing a promotional event that is tailored to your needs;</p>
  <p class="service" style="top:534px"><svg class="tick" width="21" height="17" viewBox="0 0 21 17"><path d="M0 9 L3 6 L7 10 L18 0 L21 2 L7 16 Z" fill="var(--navy)"/></svg>By representing you at trade shows or fairs;</p>
  <p class="service" style="top:564px"><svg class="tick" width="21" height="17" viewBox="0 0 21 17"><path d="M0 9 L3 6 L7 10 L18 0 L21 2 L7 16 Z" fill="var(--navy)"/></svg>By assuming the fiscal representation of your company</p>
  <p class="service" style="top:594px"><svg class="tick" width="21" height="17" viewBox="0 0 21 17"><path d="M0 9 L3 6 L7 10 L18 0 L21 2 L7 16 Z" fill="var(--navy)"/></svg>By offering you logistical and administrative support.</p>

  <svg class="hex" style="left:193px;top:632px" width="160" height="184" viewBox="0 0 160 184" role="img" aria-label="Market analysis icon">
    <polygon points="80,0 160,46 160,138 80,184 0,138 0,46" fill="var(--navy)"/>
  </svg>
  <svg class="hex" style="left:360px;top:705px" width="160" height="184" viewBox="0 0 160 184" role="img" aria-label="Distribution and logistics icon">
    <polygon points="80,0 160,46 160,138 80,184 0,138 0,46" fill="var(--navy)"/>
  </svg>
  <svg class="hex" style="left:526px;top:632px" width="160" height="184" viewBox="0 0 160 184" role="img" aria-label="Tax representation icon">
    <polygon points="80,0 160,46 160,138 80,184 0,138 0,46" fill="var(--navy)"/>
  </svg>

  <svg class="footer-band" width="927" height="1200" viewBox="0 0 927 1200">
    <polygon points="439,971 927,1104 927,1200 0,1200 0,1100" fill="var(--navy)"/>
  </svg>

  <div class="brand">
    <div class="brand-square"></div>
    <div class="brand-name">VALTERNA</div>
  </div>

  <p class="office">Neuchâtel Office Valterna Sàrl<br>Rue des Tilleuls 14 | 2012 Auvernier (Neuchâtel)</p>

  <p class="contacts">+41 (0)32 555 01 84<span class="sep">|</span>info@valterna.ch<span class="sep">|</span>www.valterna.ch</p>
</div>
</body>
</html>
```